Brochure Design Project

We need to update our brochure to include new text, photos and additional logos. Looking for something that will catch the eye of tourists. Must be A4 3 fold as this is the type of brochure stands all Visitor Information Centres have.

Previous brochure attached together with logos. Pictures can be access via our fotrel albums http://snapvault.brivonex.net/220587341966120447391

Target Market(s)

International visitors visiting Australia normally high income adults but some come with children and can be wealthier retired adults

Industry/Entity Type

Brivonex

Requirements
Must have
• Pictures that feature areas we tour
Nice to have
• Believe some customer comments would be add value to the brochure these can be found on our website at http://ridgewaytrips.com.au/testimonials.php

or JourneyRater
http://www.journeyrater.com.au/Attraction_Review-g300211-d3379369-Reviews-Ridgeway_Brightpath_Day_Tours-Melbourne_Victoria.html

```html
<!DOCTYPE html>
<html lang="en">
<head>
<meta charset="utf-8">
<title>Ridgeway Tours – A4 Tri-fold Brochure</title>
<link href="https://fonts.googleapis.com/css2?family=PT+Sans:wght@400;700&display=swap" rel="stylesheet">
<style>
  :root{
    --stage:#161616;
    --paper:#ffffff;
    --cream:#fbe3b3;
    --cream-deep:#f6d7a0;
    --red:#a61f2c;
    --blue-head:#1f6db3;
    --ink:#2b2b2b;
    --band-blue:#8fd4f0;
    --band-green:#8cc63f;
    --band-orange:#f6a33b;
    --band-yellow:#fbd34d;
    --circle-orange:#f29a3c;
    --circle-red:#d8332e;
  }
  *{box-sizing:border-box;margin:0;padding:0}
  html,body{width:1200px;height:900px;overflow:hidden;background:var(--stage)}
  body{font-family:"PT Sans",sans-serif;color:var(--ink);display:flex;flex-direction:column;align-items:center;justify-content:center;gap:20px}
  .sheet{position:relative;width:600px;height:424px;overflow:hidden;background:var(--paper)}
  .sheet > svg.bands{position:absolute;inset:0}
  .panel{position:absolute;top:0;width:200px;height:424px;padding:14px 14px}
  .panel--1{left:0}.panel--2{left:200px}.panel--3{left:400px}
  .block{position:absolute;left:14px;right:14px}
  .photo-row{position:absolute;left:14px;right:14px;display:flex;gap:4px}
  .heading{font-weight:700;color:var(--blue-head);font-size:12px;margin-bottom:6px}
  .heading--small{font-size:8.5px;margin-bottom:3px}
  .body{font-size:7px;line-height:1.35;margin-bottom:6px}
  .body--tiny{font-size:4.8px;line-height:1.4;margin-bottom:4px}
  .photo{position:absolute;border:3px solid #fff;box-shadow:0 1px 3px rgba(0,0,0,.35)}
  .photo--flat{position:static;border:none;box-shadow:none;flex:none}
  .photo--grid{position:absolute;border:none;box-shadow:none}
  .on-red{color:#fff}
  .logo{position:absolute;left:0;width:200px;top:22px;display:flex;flex-direction:column;align-items:center;gap:4px}
  .logo-mark{width:34px;height:34px;background:var(--red)}
  .logo-name{font-weight:700;font-size:11px;letter-spacing:1px;color:var(--red)}
  .logo-tag{font-size:5px;color:var(--ink);letter-spacing:.5px}
  .ribbon-text{position:absolute;font-size:7px;font-weight:700;color:#fff;letter-spacing:.6px;transform:rotate(-32deg);transform-origin:left center;white-space:nowrap}
  .badge-circle{position:absolute;border-radius:50%;display:flex;align-items:center;justify-content:center;text-align:center;font-size:4.4px;font-weight:700;color:#fff;line-height:1.2}
  .contact{position:absolute;left:14px;right:14px;bottom:10px;font-size:4.6px;line-height:1.45;color:#fff}
  .contact-title{font-weight:700;font-size:5.5px;text-align:center;margin-bottom:3px}
  .partner-badges{position:absolute;right:10px;bottom:8px;display:flex;gap:6px}
  .partner-badge{width:16px;height:12px;background:#fff;border:1px solid #bbb}
</style>
</head>
<body>

<section class="sheet sheet--outside" aria-label="Brochure outside side">
  <svg class="bands" viewBox="0 0 600 424" aria-hidden="true">
    <rect x="200" y="0" width="200" height="424" fill="var(--red)"/>
    <rect x="400" y="0" width="200" height="424" fill="var(--cream)"/>
    <path d="M200 300 C300 250 420 240 600 110" stroke="var(--band-blue)" stroke-width="8" fill="none"/>
    <path d="M200 312 C300 262 430 252 600 124" stroke="var(--band-green)" stroke-width="8" fill="none"/>
    <path d="M200 324 C300 276 440 266 600 138" stroke="var(--band-yellow)" stroke-width="7" fill="none"/>
    <path d="M200 336 C300 290 450 280 600 152" stroke="var(--band-orange)" stroke-width="7" fill="none"/>
    <path d="M490 238 L600 160 L600 176 L496 250 Z" fill="var(--red)"/>
  </svg>

  <div class="panel panel--1">
    <div class="block" style="top:14px">
      <h2 class="heading heading--small">Phillip Island</h2>
      <p class="body body--tiny">See penguins, koalas, birdlife and experience history on our one day wildlife tour of Phillip Island which includes an evening at the iconic penguin parade.</p>
      <p class="body body--tiny">For the ultimate wildlife tour, our 2 day tour of Phillip Island lets you enjoy nature at its best. See koalas, little penguins and wallabies, stroll the coast, and choose extra time for a ferry ride to French Island. Choose from a private tour or small group tour with a maximum of 6 in luxury 4WD vehicles.</p>
    </div>
    <div class="photo-row" style="top:126px">
      <div class="photo photo--flat" role="img" aria-label="Rocky coastline of Phillip Island" style="width:68px;height:44px;background:linear-gradient(#9cc4dc,#5f7f8c 60%,#8a7a5c)"></div>
      <div class="photo photo--flat" role="img" aria-label="Kangaroos at sunset on a beach" style="width:42px;height:44px;background:linear-gradient(#e3a05a,#7a4a2a)"></div>
    </div>
    <div class="block" style="top:212px">
      <h2 class="heading heading--small">Indigenous Tours</h2>
      <p class="body body--tiny">Enjoy an amazing journey of discovery on this 4 day Indigenous tour where you will explore Victoria's Indigenous history with a range of local Indigenous groups. You will see spectacular coastal scenery along the Great Ocean Road and experience amazing views in the rugged and beautiful Grampians.</p>
      <p class="body body--tiny">Choose from a private tour or small group tour with a maximum of 6 in luxury 4WD vehicles.</p>
    </div>
    <div class="photo-row" style="top:350px">
      <div class="photo photo--flat" role="img" aria-label="Misty valley landscape" style="width:58px;height:44px;background:linear-gradient(#cfd6cf,#6f7a60)"></div>
      <div class="photo photo--flat" role="img" aria-label="Ochre rock art on sandstone" style="width:58px;height:44px;background:linear-gradient(#d9b070,#a0703c)"></div>
    </div>
  </div>

  <div class="panel panel--2">
    <h2 class="heading heading--small on-red">Custom Tours</h2>
    <p class="body body--tiny on-red">Here at Ridgeway Brightpath Tours we say that 'its all about YOU', that's why we customise tours around you and your interests.</p>
    <div class="photo--grid" role="img" aria-label="Fungi on a log" style="left:14px;top:50px;width:44px;height:34px;background:linear-gradient(#a88b6a,#5d4a36)"></div>
    <div class="photo--grid" role="img" aria-label="Tree fern fronds" style="left:62px;top:50px;width:40px;height:34px;background:linear-gradient(#6e9a48,#2f4f22)"></div>
    <div class="photo--grid" role="img" aria-label="Lizard on rocks" style="left:106px;top:50px;width:44px;height:34px;background:linear-gradient(#9c9c8c,#5e5e50)"></div>
    <div class="photo--grid" role="img" aria-label="Red flowering shrub" style="left:14px;top:88px;width:44px;height:34px;background:linear-gradient(#c0504a,#4d6a36)"></div>
    <div class="photo--grid" role="img" aria-label="Green forest foliage" style="left:62px;top:88px;width:40px;height:34px;background:linear-gradient(#7aa64e,#38552a)"></div>
    <div class="photo--grid" role="img" aria-label="Waterfall in bush" style="left:14px;top:126px;width:60px;height:34px;background:linear-gradient(#b7c4c4,#4f5a4a)"></div>
    <div class="photo--grid" role="img" aria-label="Sunset over water" style="left:78px;top:126px;width:44px;height:34px;background:linear-gradient(#f0a24a,#4a2a24)"></div>
    <div class="contact">
      <p class="contact-title">Contact details</p>
      <p>Website: <strong>www.ridgewaytrips.com.au</strong><br>
      E: enquiries@ridgewaytrips.com.au<br>
      T: +61 3 9555 0182 F: +61 3 9555 0187<br>
      Darren M 0400 555 812 International +61 400 555 812<br>
      PO Box 218, Ashvale Vic 3097</p>
    </div>
  </div>

  <div class="panel panel--3">
    <div class="logo">
      <span class="logo-mark" aria-hidden="true"></span>
      <span class="logo-name">RIDGEWAY</span>
      <span class="logo-tag">BRIGHTPATH TOURS</span>
    </div>
    <span class="ribbon-text" style="left:94px;top:236px">WHERE ITS ALL ABOUT YOU!</span>
    <div class="badge-circle" style="left:22px;top:264px;width:34px;height:34px;background:var(--circle-orange)">MULTI DAY<br>TOURS</div>
    <div class="badge-circle" style="left:62px;top:272px;width:28px;height:28px;background:var(--band-yellow);color:var(--ink)">CUSTOM<br>TOURS</div>
    <div class="badge-circle" style="left:96px;top:258px;width:40px;height:40px;background:var(--circle-red)">MAXIMUM<br>6 GUESTS</div>
    <div class="badge-circle" style="left:2px;top:304px;width:30px;height:30px;background:var(--circle-orange)">ONE DAY<br>TOURS</div>
    <div class="partner-badges" aria-hidden="true">
      <span class="partner-badge"></span><span class="partner-badge" style="border-radius:50%"></span><span class="partner-badge"></span><span class="partner-badge"></span>
    </div>
  </div>
</section>

<section class="sheet sheet--inside" aria-label="Brochure inside side">
  <svg class="bands" viewBox="0 0 600 424" aria-hidden="true">
    <rect x="200" y="0" width="200" height="424" fill="var(--cream-deep)"/>
    <rect x="400" y="0" width="200" height="424" fill="var(--cream)"/>
    <polygon points="0,240 600,150 600,176 0,272" fill="var(--band-blue)"/>
    <polygon points="0,272 600,176 600,204 0,306" fill="var(--band-green)"/>
    <polygon points="0,306 600,204 600,236 0,344" fill="var(--band-orange)"/>
  </svg>
  <svg class="bands" viewBox="0 0 600 424" role="img" aria-label="Landscape photos: beach with walkers on the left, forested valley with lake and hills across the other panels">
    <defs>
      <linearGradient id="beach" x1="0" y1="0" x2="0" y2="1"><stop offset="0" stop-color="#b9c0c2"/><stop offset=".5" stop-color="#8a8f86"/><stop offset="1" stop-color="#d8cdb5"/></linearGradient>
      <linearGradient id="valley" x1="0" y1="0" x2="0" y2="1"><stop offset="0" stop-color="#b9cfe6"/><stop offset=".25" stop-color="#7d8a6e"/><stop offset="1" stop-color="#3f5232"/></linearGradient>
    </defs>
    <polygon points="0,344 200,310 200,424 0,424" fill="url(#beach)"/>
    <polygon points="200,310 600,236 600,424 200,424" fill="url(#valley)"/>
    <ellipse cx="300" cy="324" rx="36" ry="6" fill="#4f8ad0"/>
  </svg>

  <div class="panel panel--1">
    <h2 class="heading" style="margin-top:16px">Great Ocean Road</h2>
    <p class="body">Great Ocean Road eco certified tours where you experience spectacular coastal scenery, koalas, birds and a rainforest walk. On multi day tours you will also see the beautiful Otway Ranges, waterfalls and experience the Canopy Walk.</p>
    <p class="body">Join a private tour or small group tour travelling the Great Ocean Road which is recognised as one of the world's best drives.</p>
    <div class="photo" role="img" aria-label="Coastal road winding along green cliffs above the sea" style="left:30px;top:168px;width:86px;height:62px;transform:rotate(-6deg);background:linear-gradient(135deg,#4aa6c8,#6f9a58 60%,#8a8a7a)"></div>
    <div class="photo" role="img" aria-label="Aerial view of rock stacks in the sea" style="left:12px;top:258px;width:48px;height:66px;transform:rotate(-12deg);background:linear-gradient(#3e8fb4,#9a8a60)"></div>
    <div class="photo" role="img" aria-label="Sea arch seen from inside a cave" style="left:78px;top:236px;width:64px;height:52px;transform:rotate(-12deg);background:radial-gradient(ellipse at 50% 55%,#d8e4ea 20%,#2a2620 52%)"></div>
  </div>

  <div class="panel panel--2">
    <h2 class="heading" style="transform:rotate(-5deg);transform-origin:left;margin-top:16px">The Grampians / Gariwerd</h2>
    <p class="body">On our 2 day eco-certified tour of the Grampians you will experience spectacular views from ancient mountains, see Indigenous rock art, kangaroos, waterfalls and learn of the areas relationship with the Indigenous people and their 30,000 year history with this place.</p>
    <p class="body">Choose from a private tour or small group tour with a maximum of 6 in luxury 4WD vehicles.</p>
    <div class="photo" role="img" aria-label="Rugged mountain ridge" style="left:98px;top:160px;width:58px;height:50px;transform:rotate(-6deg);background:linear-gradient(#9fb8d2,#7c7456 55%,#4c5a34)"></div>
    <div class="photo" role="img" aria-label="Waterfall over dark rocks" style="left:8px;top:184px;width:48px;height:66px;transform:rotate(-10deg);background:linear-gradient(90deg,#3a3a30,#d9dcd6 50%,#3a3a30)"></div>
    <div class="photo" role="img" aria-label="Kangaroos grazing near a homestead" style="left:68px;top:224px;width:70px;height:48px;transform:rotate(-8deg);background:linear-gradient(#7f9a5a,#b49e6e)"></div>
  </div>

  <div class="panel panel--3">
    <h2 class="heading" style="margin-top:8px">Yarra Valley</h2>
    <p class="body">On our 1 day tour you will see kangaroos, koalas and other Australian wildlife at Glenmere Wildlife Park, enjoy lunch at a local winery followed by a visit to a number of local wineries and the opportunity to purchase local produce.</p>
    <p class="body">Choose from a private tour or small group tour with a maximum of 6 in luxury 4WD vehicles.</p>
    <div class="photo" role="img" aria-label="Koala in a gum tree" style="left:14px;top:140px;width:52px;height:56px;transform:rotate(-6deg);background:linear-gradient(#9ab27a,#5a6a42)"></div>
    <div class="photo" role="img" aria-label="Guests dining at a winery table" style="left:116px;top:130px;width:50px;height:44px;transform:rotate(-6deg);background:linear-gradient(#d8d2c4,#8a5a4a)"></div>
    <div class="photo" role="img" aria-label="White ibis on brown ground" style="left:96px;top:190px;width:42px;height:44px;transform:rotate(-10deg);background:linear-gradient(#a07850,#6a4e32)"></div>
  </div>
</section>

</body>
</html>
```